Business Card Design

Looking for business card designs for a new business. there will be two cards of the same design (both lots of information below in contact info). We would like the logo diagonally across the card with the information split above and below the logo similar to sketch. happy to look at similar alternatives
Please use same colours as in logo design

Industry/Entity Type

Business

Contact Information for Business Card

Dwight Halloran
mob - 0491 738 204
ph - 02 6148 3920
fax - 02 6148 3975
email - dwight@kestrelbeams.com.au
14 Larkmoor Road, Taminda NSW 2340

Colin Marchetti
mob - 0438 912 557
ph - 02 6148 3920
fax - 02 6148 3975
email - colin@kestrelbeams.com.au

```html
<!DOCTYPE html>
<html lang="en">
<head>
<meta charset="utf-8">
<title>Kestrel Beams – Business Card</title>
<link rel="stylesheet" href="https://fonts.googleapis.com/css2?family=PT+Sans:wght@400;700&display=swap">
<style>
  :root {
    --teal: #0f7874;
    --teal-text: #2a7c7a;
    --ink: #111111;
    --paper: #ffffff;
    --backdrop: #e9e6e1;
    --rule: #1a1a1a;
  }
  * { box-sizing: border-box; margin: 0; padding: 0; }
  html, body {
    width: 1145px; height: 1200px; overflow: hidden;
    background: var(--backdrop);
    font-family: "PT Sans", "Myriad Pro", Arial, sans-serif;
  }
  .stage { position: relative; width: 1145px; height: 1200px; }

  .card { position: absolute; width: 945px; height: 538px; overflow: hidden; }

  /* Front */
  .card--front {
    left: 30px; top: 45px;
    background: var(--paper);
    border: 1px solid #555;
  }
  .brand-name {
    position: absolute;
    font-weight: 700; color: var(--ink);
    letter-spacing: -1px; line-height: 1; white-space: nowrap;
  }
  .card--front .brand-name { left: 52px; top: 70px; font-size: 94px; }

  .holder-name {
    position: absolute; left: 50px; top: 244px;
    font-size: 29px; font-weight: 700; color: var(--teal-text);
  }
  .contact-list {
    position: absolute; left: 48px; top: 304px;
    list-style: none;
  }
  .contact-list li {
    display: flex; align-items: center; gap: 6px;
    height: 35px;
    font-size: 22px; color: #2b2b2b;
  }
  .contact-list svg { width: 20px; height: 20px; fill: var(--teal); flex: none; }

  .double-rule {
    position: absolute; left: 0; right: 0; top: 468px;
    height: 8px;
    border-top: 3px solid var(--rule);
    border-bottom: 2px solid var(--rule);
  }
  .address-band {
    position: absolute; left: 0; right: 0; bottom: 0; height: 58px;
    background: var(--teal);
    color: var(--paper);
    font-size: 27px; letter-spacing: 0.5px;
    padding-left: 48px; display: flex; align-items: center;
  }

  /* Back */
  .card--back {
    left: 178px; top: 621px;
    background: var(--teal);
  }
  .card--back .brand-name {
    left: 0; right: 0; top: 190px; text-align: center;
    font-size: 104px;
  }
  .web-address {
    position: absolute; left: 0; right: 0; top: 424px;
    text-align: center;
    color: var(--paper); font-size: 31px; letter-spacing: 2.5px;
  }
  .web-address strong { font-weight: 700; }
</style>
</head>
<body>
<main class="stage">

  <section class="card card--front" aria-label="Business card front">
    <div class="brand-name">Kestrel Beams</div>

    <h1 class="holder-name">Colin Marchetti</h1>

    <ul class="contact-list">
      <li>
        <svg viewBox="0 0 20 20" aria-hidden="true"><path d="M10 1a9 9 0 1 0 0 18 9 9 0 0 0 0-18zm0 2a7 7 0 1 1 0 14 7 7 0 0 1 0-14zM7 6c-1 1-1 3 .5 5s3.5 3.5 5 3l1-1.2-2-1.6-.9.8c-.8-.4-1.8-1.4-2.2-2.2l.8-.9L7.6 6.8z"/></svg>
        02 6148 3920
      </li>
      <li>
        <svg viewBox="0 0 20 20" aria-hidden="true"><path d="M6 1h8a1 1 0 0 1 1 1v16a1 1 0 0 1-1 1H6a1 1 0 0 1-1-1V2a1 1 0 0 1 1-1zm1 3v5h6V4zm0 7v2h2v-2zm4 0v2h2v-2zm-4 3v2h2v-2zm4 0v2h2v-2z"/></svg>
        0438 912 557
      </li>
      <li>
        <svg viewBox="0 0 20 20" aria-hidden="true"><path d="M5 3h8l2 4h3a1 1 0 0 1 1 1v8H1V8a1 1 0 0 1 1-1h3zm1 2v2h7l-1-2zM4 10v2h3v-2zm5 0v2h3v-2zM2 17h16v1H2z"/></svg>
        02 6148 3975
      </li>
      <li>
        <svg viewBox="0 0 20 20" aria-hidden="true"><path d="M10 2 1 8v10h18V8zm0 2.4L16.5 8 10 12 3.5 8z"/></svg>
        colin@kestrelbeams.com.au
      </li>
    </ul>

    <div class="double-rule"></div>
    <div class="address-band">14 Larkmoor Road, Corrabel NSW 2391</div>
  </section>

  <section class="card card--back" aria-label="Business card back">
    <div class="brand-name">Kestrel Beams</div>
    <p class="web-address">www.<strong>kestrelbeams</strong>.com.au</p>
  </section>

</main>
</body>
</html>
```